Keystone Trench Co Business Card*

Looking for a professional, clean and crisp business card

I am in the underground utilities industry and am just looking for a really impressive business card. I would like our card to be white with our symbol crisp and clear with it protruding. I also have a business partner that will require his name and info on the card once the design is set. I would like to have our website info on the card which is;
http://keystonetrenchco.example/

Contact Information for Business Card

Website, contact name, number and email

```html
<!DOCTYPE html>
<html lang="en">
<head>
<meta charset="utf-8">
<title>Keystone Trench Co — Business Card</title>
<link href="https://fonts.googleapis.com/css2?family=Questrial&family=Saira+Condensed:wght@700&display=swap" rel="stylesheet">
<style>
  :root {
    --stage-top: #3a3a3a;
    --stage-bottom: #141414;
    --card-black: #07080a;
    --pattern-dark: #0c0e12;
    --pattern-light: #1b1f26;
    --slate: #323d4d;
    --paper: #ffffff;
    --ink: #2a2f3a;
    --accent-blue: #3558a8;
    --mark-white: #ffffff;
  }
  * { box-sizing: border-box; margin: 0; padding: 0; }
  html, body { width: 1200px; height: 900px; overflow: hidden; }
  body {
    background: radial-gradient(ellipse at 50% 30%, var(--stage-top), var(--stage-bottom) 75%);
    display: flex;
    flex-direction: column;
    align-items: center;
    justify-content: center;
    gap: 40px;
  }
  .card {
    position: relative;
    width: 630px;
    height: 360px;
    overflow: hidden;
    box-shadow: 0 12px 30px rgba(0,0,0,0.55);
  }

  /* Front side */
  .card-front { background: var(--card-black); }
  .card-front .texture {
    position: absolute; inset: 0;
    background: linear-gradient(135deg, var(--pattern-dark) 0%, var(--pattern-light) 50%, var(--pattern-dark) 100%);
  }
  .brand-lockup {
    position: absolute;
    left: 50%; top: 50%;
    transform: translate(-50%, -50%);
    display: flex;
    align-items: center;
    gap: 14px;
  }
  .brand-dot {
    width: 30px; height: 30px;
    border-radius: 50%;
    background: var(--accent-blue);
    flex: none;
  }
  .brand-name {
    font-family: "Saira Condensed", sans-serif;
    font-weight: 700;
    font-size: 38px;
    letter-spacing: 1px;
    text-transform: uppercase;
    color: var(--mark-white);
    white-space: nowrap;
  }

  /* Contact side */
  .card-back { background: var(--paper); }
  .card-back .split { position: absolute; inset: 0; }
  .card-back .brand-lockup {
    left: 540px; top: 58px;
    transform: translateX(-50%);
    flex-direction: column;
    gap: 8px;
  }
  .card-back .brand-dot { width: 22px; height: 22px; }
  .card-back .brand-name {
    font-size: 32px;
    line-height: 1.05;
    text-align: center;
    white-space: normal;
  }

  .contact-block {
    position: absolute;
    left: 40px;
    top: 160px;
  }
  .person-name {
    font-family: "Saira Condensed", sans-serif;
    font-weight: 700;
    font-size: 30px;
    letter-spacing: 1px;
    text-transform: uppercase;
    color: var(--ink);
  }
  .name-rule {
    width: 18px; height: 2px;
    background: var(--accent-blue);
    margin: 14px 0 22px;
  }
  .contact-list { list-style: none; }
  .contact-item {
    display: flex;
    align-items: center;
    gap: 10px;
    font-family: "Questrial", sans-serif;
    font-size: 17px;
    color: var(--ink);
    line-height: 1.65;
  }
  .contact-item svg { width: 16px; height: 16px; flex: none; }
  .web-domain { color: var(--accent-blue); }
</style>
</head>
<body>

  <section class="card card-front" aria-label="Card front">
    <div class="texture" role="img" aria-label="Dark diagonal pipe pattern background"></div>
    <div class="brand-lockup">
      <span class="brand-dot"></span>
      <span class="brand-name">Keystone Trench Co</span>
    </div>
  </section>

  <section class="card card-back" aria-label="Card contact side">
    <svg class="split" viewBox="0 0 630 360" preserveAspectRatio="none" aria-hidden="true">
      <polygon points="290,0 335,0 600,360 555,360" fill="var(--slate)"/>
      <polygon points="340,0 630,0 630,360 605,360" fill="var(--card-black)"/>
    </svg>

    <div class="brand-lockup">
      <span class="brand-dot"></span>
      <span class="brand-name">Keystone<br>Trench Co</span>
    </div>

    <div class="contact-block">
      <h1 class="person-name">Dale Morrow</h1>
      <div class="name-rule"></div>
      <ul class="contact-list">
        <li class="contact-item">
          <svg viewBox="0 0 16 16" fill="none" stroke="var(--accent-blue)" stroke-width="1.3">
            <circle cx="8" cy="8" r="7"/>
            <path d="M5.5 4.5l1.2 1.8-.8.9c.6 1.2 1.6 2.2 2.8 2.8l.9-.8 1.8 1.2-.8 1.3c-2.8-.3-5.1-2.6-5.4-5.4z"/>
          </svg>
          <span>555-014-2280</span>
        </li>
        <li class="contact-item">
          <svg viewBox="0 0 16 16" fill="none" stroke="var(--accent-blue)" stroke-width="1.3">
            <rect x="1.5" y="3.5" width="13" height="9"/>
            <path d="M1.5 3.5l6.5 5 6.5-5"/>
          </svg>
          <span>Dale@keystonetrenchco.example</span>
        </li>
        <li class="contact-item">
          <svg viewBox="0 0 16 16" fill="none" stroke="var(--accent-blue)" stroke-width="1.3">
            <circle cx="8" cy="8" r="6.5"/>
            <ellipse cx="8" cy="8" rx="3" ry="6.5"/>
            <path d="M1.5 8h13M2.5 5h11M2.5 11h11"/>
          </svg>
          <span>www.<span class="web-domain">keystonetrenchco</span>.example</span>
        </li>
      </ul>
    </div>
  </section>

</body>
</html>
```